Business Card Design Project - del varosi group

dear Sirs

we need business card design for our group ( DEL Varosi Group ) , i have got the Logo design of our group from pixel harbor in previous , so all need details relating to our group i think available with you, as well as the the chosen logo design

we hope to provide us with business card logo that to be appropaite and satisfactory to us .

thanks

note : logo design of our group is attached .
Updates

Reason: please extend the deadline of my project for additional 15 days because i didn't received appropriate design for our gruop yet . kindly beaware that i have received 77 design till now , supossed to send me 200-250 design at least . thanks

Target Market(s)

contents

name : Kerem EL Nadiri

position : Operation Manager

Industry/Entity Type

Business

Requirements
Must have

• person name

group logo
Nice to have
• logo color matching with back background

```html
<!DOCTYPE html>
<html lang="en">
<head>
<meta charset="utf-8">
<title>DEL Varosi Group – Business Card</title>
<link href="https://fonts.googleapis.com/css2?family=Open+Sans:wght@400;600;700&display=swap" rel="stylesheet">
<style>
  :root {
    --stage: #b48c2c;
    --paper: #ffffff;
    --brand-blue: #1b5c9e;
    --bright-blue: #1a7cc1;
    --deep-blue: #0d4a8a;
    --gold: #c0962f;
    --gold-light: #e3c574;
    --ink: #1c1c1c;
  }
  * { margin: 0; padding: 0; box-sizing: border-box; }
  html, body { width: 1200px; height: 686px; overflow: hidden; }
  body {
    background: var(--stage);
    font-family: "Open Sans", sans-serif;
    position: relative;
  }
  .card {
    position: absolute;
    width: 524px;
    height: 300px;
    overflow: hidden;
  }
  .card--front { left: 63px; top: 128px; background: var(--paper); }
  .card--back {
    left: 611px; top: 298px;
    background: radial-gradient(ellipse at 50% 45%, var(--gold-light) 0%, #d7b054 45%, var(--gold) 100%);
    display: flex; align-items: center; justify-content: center;
  }
  .accent { position: absolute; }
  .accent--top-bar {
    left: 180px; top: 0; width: 320px; height: 10px;
    background: linear-gradient(90deg, var(--deep-blue), var(--bright-blue) 60%, var(--deep-blue));
  }
  .accent--top-block { left: 461px; top: 0; width: 63px; height: 21px; background: var(--gold); }
  .accent--side-block { left: 0; top: 240px; width: 22px; height: 60px; background: var(--gold); }
  .accent--side-bar {
    left: 0; top: 215px; width: 10px; height: 67px;
    background: linear-gradient(180deg, var(--deep-blue), var(--bright-blue));
  }
  .brand {
    display: flex; align-items: center; gap: 8px;
    color: var(--brand-blue);
    font-weight: 700;
    letter-spacing: 0.5px;
    white-space: nowrap;
  }
  .brand__mark { width: 14px; height: 14px; background: var(--brand-blue); flex: none; }
  .card--front .brand { position: absolute; left: 74px; top: 76px; font-size: 26px; }
  .card--back .brand { font-size: 30px; margin-left: -20px; }
  .card--back .brand__mark { width: 16px; height: 16px; }
  .contact {
    position: absolute; right: 50px; top: 88px;
    text-align: right;
  }
  .contact__name { color: var(--bright-blue); font-weight: 700; font-size: 15px; line-height: 22px; }
  .contact__role { color: var(--gold); font-weight: 700; font-size: 11.5px; line-height: 14px; margin-bottom: 10px; }
  .contact__list { list-style: none; }
  .contact__item {
    display: flex; justify-content: flex-end; align-items: center; gap: 5px;
    color: var(--ink); font-size: 12px; line-height: 17.5px;
  }
  .contact__item svg { width: 11px; height: 11px; fill: var(--bright-blue); flex: none; }
  .contact__address {
    margin-top: 6px; margin-right: 16px;
    font-style: normal; color: var(--ink); font-size: 12px; line-height: 14.5px;
  }
</style>
</head>
<body>
  <section class="card card--front" aria-label="Business card front">
    <div class="accent accent--top-bar"></div>
    <div class="accent accent--top-block"></div>
    <div class="accent accent--side-block"></div>
    <div class="accent accent--side-bar"></div>

    <div class="brand"><span class="brand__mark"></span>DEL Varosi Group</div>

    <div class="contact">
      <p class="contact__name">Kerem EL Nadiri</p>
      <p class="contact__role">Operation Manager</p>
      <ul class="contact__list">
        <li class="contact__item">(TF)123-456-7890
          <svg viewBox="0 0 24 24"><path d="M6.6 10.8a15 15 0 0 0 6.6 6.6l2.2-2.2c.3-.3.7-.4 1-.2 1.1.4 2.3.6 3.6.6.6 0 1 .4 1 1V20c0 .6-.4 1-1 1A17 17 0 0 1 3 4c0-.6.4-1 1-1h3.5c.6 0 1 .4 1 1 0 1.3.2 2.5.6 3.6.1.3 0 .7-.2 1z"/></svg></li>
        <li class="contact__item">123-456-7890
          <svg viewBox="0 0 24 24"><path d="M6.6 10.8a15 15 0 0 0 6.6 6.6l2.2-2.2c.3-.3.7-.4 1-.2 1.1.4 2.3.6 3.6.6.6 0 1 .4 1 1V20c0 .6-.4 1-1 1A17 17 0 0 1 3 4c0-.6.4-1 1-1h3.5c.6 0 1 .4 1 1 0 1.3.2 2.5.6 3.6.1.3 0 .7-.2 1z"/></svg></li>
        <li class="contact__item">123-456-7890
          <svg viewBox="0 0 24 24"><path d="M6 2h10v6H6zM3 9h18v10H3zm3 3v2h4v-2zm0 4v1h12v-1zM5 20h14v2H5z"/></svg></li>
        <li class="contact__item">name@website.com
          <svg viewBox="0 0 24 24"><path d="M2 5h20v14H2zm2 2v.5l8 5 8-5V7l-8 5z"/></svg></li>
        <li class="contact__item">www.website.com
          <svg viewBox="0 0 24 24"><path d="M12 2a10 10 0 1 0 0 20 10 10 0 0 0 0-20zm0 2c1 1.3 1.8 3 2.1 5H9.9C10.2 7 11 5.3 12 4zM4.3 13a8 8 0 0 1 0-2h3.6a17 17 0 0 0 0 2zm5.6 0a15 15 0 0 1 0-2h4.2a15 15 0 0 1 0 2zm6.2 0a17 17 0 0 0 0-2h3.6a8 8 0 0 1 0 2zM12 20c-1-1.3-1.8-3-2.1-5h4.2c-.3 2-1.1 3.7-2.1 5z"/></svg></li>
      </ul>
      <address class="contact__address">Street name City<br>State, zip code</address>
    </div>
  </section>

  <section class="card card--back" aria-label="Business card back">
    <div class="brand"><span class="brand__mark"></span>DEL Varosi Group</div>
  </section>
</body>
</html>
```